i need a business card for a plumbing company in california

we are a drain cleaning , maintenance plumbing company who is starting new marketing campaign for a tatrench-less pipe installation department .

Target Market(s)

the professional who appreciates time and quality workmanship.

Industry/Entity Type

Plumbing

Colors
0655a3
ec1f27

Requirements
Must have
• the second logo needs to be included
Nice to have
• a focus on the services offered
Should not have
• any underlined words on the brief

```html
<!DOCTYPE html>
<html lang="en">
<head>
<meta charset="utf-8">
<title>Pipeline Pros – Business Card</title>
<link href="https://fonts.googleapis.com/css2?family=Arimo:wght@400;700&family=Tinos:wght@400&display=swap" rel="stylesheet">
<style>
  :root{
    --blue:#0655a3;
    --navy:#0b3f7e;
    --red:#ec1f27;
    --grey:#6d6c66;
    --paper:#ffffff;
    --paper-shade:#eeeeee;
    --backdrop:#2b2b2b;
  }
  *{margin:0;padding:0;box-sizing:border-box}
  html,body{width:1200px;height:997px;overflow:hidden}
  body{background:var(--backdrop);font-family:"Arimo",Arial,sans-serif;position:relative}
  .card{position:absolute;width:540px;height:310px;border-radius:16px;overflow:hidden;
        background:linear-gradient(180deg,var(--paper) 0%,var(--paper-shade) 100%);
        box-shadow:0 20px 40px rgba(0,0,0,.5)}
  .card--front{left:40px;top:343px}
  .card--back{left:620px;top:343px}
  .card svg.art{position:absolute;inset:0}
  .brand{position:absolute;right:34px;top:18px;display:flex;align-items:center;gap:10px}
  .brand__name{font-weight:700;color:var(--grey);font-size:30px;line-height:28px;text-align:right}
  .brand__dot{width:26px;height:26px;border-radius:50%;background:var(--red)}
  .step{position:absolute;font-size:11px;font-weight:700;letter-spacing:.5px;white-space:nowrap}
  .step--red{color:var(--red)} .step--blue{color:var(--blue)}
  .motto{position:absolute;left:40px;top:280px;width:340px;height:22px;border-radius:11px;
         background:var(--blue);color:#fff;font-size:12px;line-height:22px;text-align:center}
  .person{position:absolute;right:34px;top:96px;text-align:right}
  .person__name{color:var(--red);font-weight:700;font-size:15px}
  .person__role{color:var(--blue);font-size:14px}
  .contact{position:absolute;left:22px;top:194px;color:#fff;font-family:"Tinos","Times New Roman",serif;font-size:15px}
  .contact__email{padding-left:150px;height:20px;line-height:20px;white-space:nowrap}
  .contact__row{display:flex;align-items:center;gap:8px;height:22px;white-space:nowrap}
  .contact__num{width:17px;height:17px;border-radius:50%;background:#fff;color:var(--navy);
                font-family:"Arimo",Arial,sans-serif;font-weight:700;font-size:11px;
                display:flex;align-items:center;justify-content:center}
  .services{position:absolute;left:22px;right:22px;top:284px;color:#fff;font-weight:700;font-size:15px;line-height:18px;text-align:center;white-space:nowrap}
</style>
</head>
<body>

<section class="card card--front">
  <svg class="art" width="540" height="310" viewBox="0 0 540 310">
    <path d="M0 232 C150 222 200 162 300 152 S450 102 540 52" fill="none" stroke="var(--red)" stroke-width="10"/>
    <path d="M0 242 C150 232 200 172 300 162 S450 112 540 62" fill="none" stroke="var(--blue)" stroke-width="10"/>
    <g font-family="Tinos, serif" font-size="26" fill="#fff" text-anchor="middle">
      <circle cx="90" cy="233" r="23" fill="var(--blue)" stroke="#fff" stroke-width="3"/>
      <text x="90" y="242">1</text>
      <circle cx="255" cy="167" r="23" fill="var(--blue)" stroke="#fff" stroke-width="3"/>
      <text x="255" y="176">2</text>
      <circle cx="420" cy="116" r="23" fill="var(--blue)" stroke="#fff" stroke-width="3"/>
      <text x="420" y="125">3</text>
    </g>
  </svg>
  <div class="brand"><div class="brand__name">Pipeline<br>Pros</div><div class="brand__dot"></div></div>
  <div class="step step--red" style="left:52px;top:262px">CONTACT US</div>
  <div class="step step--blue" style="left:222px;top:198px">BUY ONLINE</div>
  <div class="step step--red" style="left:370px;top:146px">SOCIAL MEDIA US</div>
  <div class="motto">I am reminding myself to always lead by example.</div>
</section>

<section class="card card--back">
  <svg class="art" width="540" height="310" viewBox="0 0 540 310">
    <path d="M0 170 C120 142 220 160 330 155 S480 128 540 118 L540 310 L0 310 Z" fill="var(--red)"/>
    <path d="M0 186 C120 158 220 174 330 168 S480 140 540 132 L540 310 L0 310 Z" fill="var(--navy)"/>
  </svg>
  <div class="brand"><div class="brand__name">Pipeline<br>Pros</div><div class="brand__dot"></div></div>
  <div class="person"><div class="person__name">Marco Delgado</div><div class="person__role">Owner</div></div>
  <div class="contact">
    <div class="contact__email">info@pipelinepros.com</div>
    <div class="contact__row"><span class="contact__num">1</span>209 555-0142 &nbsp; hello@pipelinepros.com</div>
    <div class="contact__row"><span class="contact__num">2</span>www.PipelinePros.com</div>
    <div class="contact__row"><span class="contact__num">3</span>@PipelinePros</div>
  </div>
  <div class="services">Sewer Drain Cleaning —Maintenance— Trenchless Re-Pipes</div>
</section>

</body>
</html>
```